Trendy eye catching business card for lawn mowing business

Turf Tidy, a local community lawn mowing service, requires an eye catching trendy business card to drop into letterboxes.

We could simply throw something together from a Microsoft Word template, but we are wanting something more than this. Some other business’ images are attached for some inspiration.

We are requiring the card to have Turf Tidy with our slogan, Call The Brindles. In addition, provide details with that we are a local, affordable lawn mowing service, and for other gardening matters to simply just ask!
Plus the relevant contact details, phone, email, social media.

Target Market(s)

Local community members who require assistance with their garden care

Industry/Entity Type

Gardening

Contact Information for Business Card

the name TURF TIDY is our logo
telephone logo 0438 215 967
email logo turftidy@postbox-mail.example
Instagram logo turftidy
Facebook logo turftidy.sth
Lawn Mowing Service
Local Affordable
edge trim, blow and clipping removal included.
Other gardening matters, just ask!

Font styles to use
Serif
Sans Serif
Decorative
Script

Colors
9bcb3c
ffffff

Requirements
Must have
• All the details listed in Business Card Details.
Make these words prominent:
Turf Tidy
Lawn Mowing Service
Local
Affordable
Nice to have
• Our slogan ‘Call The Brindles’ incorporated.
Different colour background for front and reverse side
Greens, white and black colours
Subtle grass blades images incorporated
Should not have
• No images of lawnmowers.
No images of men/cartoons.
No using initials for Turf Tidy

```html
<!DOCTYPE html>
<html lang="en">
<head>
<meta charset="utf-8">
<title>Turf Tidy – Business Card</title>
<link rel="stylesheet" href="https://fonts.googleapis.com/css2?family=Exo+2:wght@300;600;700&family=Roboto:wght@400;500;700&display=swap">
<style>
  :root {
    --grass: #8cc63f;
    --grass-deep: #5e9a23;
    --ink: #1c1c1c;
    --card-dark: #1f1f1f;
    --paper: #ffffff;
    --muted: #8a8a8a;
    --stage: #d6d6d6;
  }
  * { margin: 0; padding: 0; box-sizing: border-box; }
  html, body { width: 1200px; height: 802px; overflow: hidden; }
  body {
    background: var(--stage);
    font-family: "Roboto", Arial, sans-serif;
    position: relative;
  }
  .card {
    position: absolute;
    top: 240px;
    width: 540px;
    height: 322px;
    overflow: hidden;
  }
  .card--front { left: 40px; background: var(--paper); }
  .card--back { left: 620px; background: var(--card-dark); color: var(--paper); }

  .front-band { position: absolute; left: 0; top: 0; width: 190px; height: 322px; }
  .grass-art {
    position: absolute;
    bottom: 0;
  }
  .grass-art--front {
    left: 8px; width: 170px; height: 230px;
    background: linear-gradient(90deg, rgba(140,198,63,0.15), rgba(140,198,63,0.85) 55%, rgba(140,198,63,0.25));
    border-radius: 60px 60px 0 0;
  }
  .grass-art--back-left {
    left: 0; width: 110px; height: 165px;
    background: linear-gradient(180deg, rgba(140,198,63,0), rgba(140,198,63,0.75));
  }
  .grass-art--back-right {
    right: 0; width: 110px; height: 165px;
    background: linear-gradient(180deg, rgba(140,198,63,0), rgba(140,198,63,0.75));
  }

  .brand {
    position: absolute;
    text-align: center;
  }
  .card--front .brand { left: 235px; width: 218px; top: 100px; }
  .card--back .brand { left: 120px; width: 300px; top: 225px; }
  .brand__name {
    font-family: "Exo 2", Arial, sans-serif;
    font-weight: 700;
    color: var(--grass);
    letter-spacing: 0.5px;
    line-height: 1;
  }
  .card--front .brand__name { font-size: 32px; }
  .card--back .brand__name { font-size: 38px; }
  .brand__tagline {
    display: flex;
    align-items: center;
    gap: 6px;
    font-family: "Roboto", Arial, sans-serif;
    font-weight: 500;
    text-transform: uppercase;
    color: var(--muted);
    white-space: nowrap;
    margin-top: 6px;
  }
  .card--front .brand__tagline { font-size: 10.5px; letter-spacing: 1.4px; }
  .card--back .brand__tagline { font-size: 14px; letter-spacing: 2px; color: #b5b5b5; }
  .brand__tagline::before, .brand__tagline::after {
    content: ""; flex: 1; height: 1px; background: currentColor;
  }

  .contact-list {
    position: absolute;
    left: 240px; top: 204px;
    list-style: none;
    font-size: 15px;
    color: var(--ink);
  }
  .contact-list li { display: flex; align-items: center; gap: 6px; height: 20px; }
  .contact-list li.gap { margin-top: 11px; }
  .contact-icon { width: 16px; height: 16px; flex: none; }

  .service { position: absolute; left: 0; width: 540px; text-align: center; }
  .service__title { top: 58px; font-size: 27px; font-weight: 700; letter-spacing: 0.3px; }
  .service__pitch { top: 90px; font-size: 24px; color: var(--grass); }
  .service__detail { top: 132px; font-size: 18px; line-height: 23px; }
  .service__phone {
    top: 180px; font-family: "Exo 2", Arial, sans-serif; font-weight: 300;
    font-size: 25px; letter-spacing: 1.5px; color: var(--grass);
  }
</style>
</head>
<body>

<section class="card card--front" aria-label="Business card front">
  <svg class="front-band" viewBox="0 0 190 322" aria-hidden="true">
    <path d="M0 0 H150 C110 60 95 170 115 322 H0 Z" fill="var(--ink)"/>
  </svg>
  <div class="grass-art grass-art--front" role="img" aria-label="Tall green grass blades rising from the bottom edge"></div>

  <div class="brand">
    <div class="brand__name">TURF TIDY</div>
    <div class="brand__tagline">Call The Brindles</div>
  </div>

  <ul class="contact-list">
    <li>
      <svg class="contact-icon" viewBox="0 0 16 16" aria-hidden="true">
        <rect x="0.5" y="0.5" width="15" height="15" rx="2" fill="none" stroke="var(--grass)"/>
        <path d="M5 3.5 L6.6 5.6 L5.6 6.8 C6.3 8.4 7.6 9.7 9.2 10.4 L10.4 9.4 L12.5 11 L11.5 12.6 C7.5 12.4 3.6 8.5 3.4 4.5 Z" fill="var(--grass)"/>
      </svg>
      0438 215 967
    </li>
    <li>
      <svg class="contact-icon" viewBox="0 0 16 16" aria-hidden="true">
        <rect x="0.5" y="3" width="15" height="10" fill="var(--grass)"/>
        <path d="M0.5 3 L8 9 L15.5 3" fill="none" stroke="var(--paper)" stroke-width="1.2"/>
      </svg>
      turftidy@postbox-mail.example
    </li>
    <li class="gap">
      <svg class="contact-icon" viewBox="0 0 16 16" aria-hidden="true">
        <circle cx="8" cy="8" r="7" fill="none" stroke="var(--grass)" stroke-width="1.4"/>
      </svg>
      @turftidy
    </li>
    <li>
      <svg class="contact-icon" viewBox="0 0 16 16" aria-hidden="true">
        <circle cx="8" cy="8" r="7" fill="none" stroke="var(--grass)" stroke-width="1.4"/>
      </svg>
      turftidy.sth
    </li>
  </ul>
</section>

<section class="card card--back" aria-label="Business card back">
  <div class="grass-art grass-art--back-left" role="img" aria-label="Green grass blades in the lower left corner"></div>
  <div class="grass-art grass-art--back-right" role="img" aria-label="Green grass blades in the lower right corner"></div>

  <h1 class="service service__title">LAWN MOWING SERVICE</h1>
  <p class="service service__pitch">Local. Affordable.</p>
  <p class="service service__detail">Edge trim, blow and clipping removal included.<br>Other gardening matters, just ask!</p>
  <p class="service service__phone">0438 215 967</p>

  <div class="brand">
    <div class="brand__name">TURF TIDY</div>
    <div class="brand__tagline">Call The Brindles</div>
  </div>
</section>

</body>
</html>
```